New Business Card Design Project LORVANTI-Italy

we are LORVANTI-Italy
our company in the market for 3 years we are luxury cosmetic company and its about time for a facelift :)
i will like to have elegant luxurious and unique business card
that will give the person that get it a unique, luxurious and elegant impression
I'm VERY OPEN FOR NEW IDEAS , even duo i add a few files of things that i see on line and i like them

i add my logo as well
my website is LORVANTI.COM
(if you would like to see the main style that we have)

Target Market(s)

adult that have money :)

Industry/Entity Type

Business

Contact Information for Business Card

Name - Dario Lorvanti
Position - CEO and CO Founder
address - 4817 E Halvern
telephone - 555-384-1926
email - dario@lorvanti.com
fax - 555-384-1926
website - LORVANTI.COM

Colors
000000
959595
fbee3e
ffffff

Requirements
Must have
• big logo in GOLD color
• elegant look
• impressive
Nice to have
• not must but maybe classy pattern background
• not must but maybe emblem
• maybe clear plastic business card
Should not have
• colors
• images

```html
<!DOCTYPE html>
<html lang="en">
<head>
<meta charset="utf-8">
<title>LORVANTI-Italy Business Card</title>
<link rel="stylesheet" href="https://fonts.googleapis.com/css2?family=Open+Sans:wght@400;600&display=swap">
<style>
  :root {
    --backdrop: #3a322d;
    --card: #0d0d0e;
    --card-edge: #1c1c1e;
    --gold: #d6a934;
    --white: #f4f4f4;
    --silver: #959595;
    --rule: #cfcfcf;
  }
  * { margin: 0; padding: 0; box-sizing: border-box; }
  html, body { width: 1200px; height: 864px; overflow: hidden; }
  body {
    background: var(--backdrop);
    font-family: "Open Sans", Arial, sans-serif;
    display: flex;
    align-items: center;
    justify-content: center;
    gap: 40px;
  }
  .card {
    position: relative;
    width: 540px;
    height: 309px;
    background: var(--card);
    border: 1px solid var(--card-edge);
    border-radius: 3px;
    box-shadow: 0 12px 30px rgba(0,0,0,.45);
    color: var(--white);
  }

  /* Back side */
  .card-back .emblem {
    position: absolute;
    left: 50%;
    top: 92px;
    transform: translateX(-50%);
    display: flex;
    flex-direction: column;
    align-items: center;
    gap: 12px;
  }
  .card-back .emblem-ring {
    width: 64px; height: 64px;
    border: 2px solid var(--silver);
    border-radius: 50%;
  }
  .card-back .emblem-name {
    color: var(--silver);
    font-size: 18px;
    font-weight: 600;
    letter-spacing: 4px;
  }
  .card-back .web {
    position: absolute;
    left: 40px;
    bottom: 34px;
    color: var(--silver);
    font-size: 13px;
    letter-spacing: 4px;
  }

  /* Front side */
  .card-front .person { position: absolute; left: 36px; top: 92px; }
  .card-front .name { color: var(--gold); font-size: 19px; font-weight: 600; }
  .card-front .role { font-size: 15px; margin-top: 2px; }
  .card-front .contacts {
    position: absolute; left: 36px; top: 150px;
    list-style: none; font-size: 12.5px;
  }
  .card-front .contacts li { display: flex; align-items: center; gap: 7px; height: 18px; }
  .card-front .contacts svg { width: 11px; height: 11px; fill: var(--gold); }
  .card-front .rule {
    position: absolute; left: 36px; right: 36px; top: 222px;
    height: 1px; background: var(--rule);
  }
  .card-front .brand {
    position: absolute; right: 40px; top: 110px;
    display: flex; flex-direction: column; align-items: center; gap: 10px;
  }
  .card-front .brand-ring {
    width: 52px; height: 52px;
    border: 2px solid var(--gold);
    border-radius: 50%;
  }
  .card-front .brand-name {
    color: var(--gold); font-size: 22px; font-weight: 600; letter-spacing: 1px;
  }
  .card-front .address {
    position: absolute; right: 36px; top: 240px;
    text-align: right; font-size: 13px; line-height: 19px;
  }
  .card-front .address .site { font-size: 14px; }
</style>
</head>
<body>
  <section class="card card-back" aria-label="Business card back">
    <div class="emblem">
      <div class="emblem-ring"></div>
      <div class="emblem-name">LORVANTI-Italy</div>
    </div>
    <div class="web">www.lorvanti.com</div>
  </section>

  <section class="card card-front" aria-label="Business card front">
    <div class="person">
      <div class="name">Dario Lorvanti</div>
      <div class="role">CEO &amp; CO Founder</div>
    </div>
    <ul class="contacts">
      <li>
        <svg viewBox="0 0 12 12" aria-hidden="true"><path d="M2.5 1h2l1 2.5-1.3 1a6 6 0 0 0 3.3 3.3l1-1.3L11 7.5v2A1.5 1.5 0 0 1 9.5 11 8.5 8.5 0 0 1 1 2.5 1.5 1.5 0 0 1 2.5 1z"/></svg>
        555-384-1926
      </li>
      <li>
        <svg viewBox="0 0 12 12" aria-hidden="true"><rect x="3" y="1" width="6" height="3"/><rect x="1" y="5" width="10" height="5" rx="1"/></svg>
        555-384-1926
      </li>
      <li>
        <svg viewBox="0 0 12 12" aria-hidden="true"><path d="M1 2.5h10v7H1z M1 3l5 3.5L11 3" /></svg>
        dario@lorvanti.com
      </li>
    </ul>
    <div class="brand">
      <div class="brand-ring"></div>
      <div class="brand-name">LORVANTI-Italy</div>
    </div>
    <div class="rule"></div>
    <div class="address">
      <div>4817 E Halvern</div>
      <div class="site">WWW.LORVANTI.COM</div>
    </div>
  </section>
</body>
</html>
```